​Silver Harbor Rhythm provides personal, friendly service in a fun and high energy environment. We are based in Vermont.

We would like a card that appeals to a wide range of audiences as we do a wide range of events. Please feel free to check out our website silverharborrhythm.net for inspiration.

Target Market(s)

weddings, corporate, birthday parties, colleges

Industry/Entity Type

Business

Contact Information for Business Card

Silver Harbor Rhythm
Providing Entertainment For All Occasions
555 274 9160
silverharborrhythm@mailnest.net
silverharborrhythm.net

```html
<!DOCTYPE html>
<html lang="en">
<head>
<meta charset="utf-8">
<title>Silver Harbor Rhythm – Business Card</title>
<link href="https://fonts.googleapis.com/css2?family=Open+Sans:wght@400;600;700&display=swap" rel="stylesheet">
<style>
  :root {
    --bg: #e9e5df;
    --card-white: #ffffff;
    --brand-green: #3f6e1e;
    --ink-dark: #1b1b1b;
    --text-grey: #555555;
    --rule-grey: #d6d6d6;
    --back-dark: #160708;
    --back-text: #ffffff;
  }
  * { box-sizing: border-box; margin: 0; padding: 0; }
  html, body {
    width: 1200px; height: 829px; overflow: hidden;
    background: var(--bg);
    font-family: "Open Sans", Arial, sans-serif;
  }
  .stage { position: relative; width: 1200px; height: 829px; }
  .card {
    position: absolute; top: 266px;
    width: 520px; height: 297px;
    overflow: hidden;
    box-shadow: 0 6px 18px rgba(0,0,0,0.18);
  }
  /* Front */
  .card-front { left: 60px; background: var(--card-white); }
  .front-art { position: absolute; inset: 0; }
  .brand {
    position: absolute; left: 34px; top: 104px;
    display: flex; align-items: center; gap: 10px;
    color: var(--brand-green); font-weight: 700;
    font-size: 20px; line-height: 1.15; letter-spacing: 0.5px; text-transform: uppercase;
  }
  .brand-mark { width: 14px; height: 14px; background: var(--brand-green); flex: none; }
  .divider {
    position: absolute; left: 292px; top: 40px;
    width: 1px; height: 92px; background: var(--rule-grey);
  }
  .contact { position: absolute; left: 306px; top: 40px; color: var(--text-grey); }
  .contact-name { color: var(--brand-green); font-weight: 700; font-size: 16px; line-height: 1.2; }
  .contact-title { font-size: 12px; margin-bottom: 10px; }
  .contact-line { display: flex; align-items: center; gap: 6px; font-size: 10.5px; line-height: 1.7; }
  .contact-line svg { width: 10px; height: 10px; flex: none; }
  .front-url {
    position: absolute; right: 16px; top: 200px;
    color: var(--back-text); font-size: 12px; letter-spacing: 0.3px;
  }
  .address {
    position: absolute; left: 24px; top: 234px;
    color: var(--text-grey); font-size: 11.5px;
  }
  /* Back */
  .card-back { left: 620px; background: var(--back-dark); }
  .back-brand {
    position: absolute; left: 0; right: 0; top: 112px;
    display: flex; justify-content: center; align-items: center; gap: 12px;
    color: var(--back-text); font-weight: 700; font-size: 30px;
    letter-spacing: 1px; text-transform: uppercase;
  }
  .back-brand .brand-mark { width: 18px; height: 18px; background: var(--back-text); }
  .back-url {
    position: absolute; right: 28px; bottom: 28px;
    color: var(--back-text); font-size: 17px; letter-spacing: 0.6px;
  }
</style>
</head>
<body>
<main class="stage">
  <section class="card card-front" aria-label="Card front">
    <svg class="front-art" viewBox="0 0 520 297" aria-hidden="true">
      <path d="M255 258 C305 258 310 186 360 186 L520 186 L520 258 Z" fill="var(--brand-green)"/>
      <rect x="0" y="258" width="520" height="18" fill="var(--ink-dark)"/>
      <rect x="0" y="276" width="520" height="21" fill="var(--brand-green)"/>
    </svg>
    <div class="brand"><span class="brand-mark"></span><span>Silver Harbor<br>Rhythm</span></div>
    <div class="divider"></div>
    <div class="contact">
      <div class="contact-name">Your Name</div>
      <div class="contact-title">Title</div>
      <div class="contact-line">
        <svg viewBox="0 0 10 10"><path d="M2 1 L4 3 L3 4 Q4 6 6 7 L7 6 L9 8 L8 9.5 Q2 9 0.5 2 Z" fill="var(--brand-green)"/></svg>
        555 274 9160
      </div>
      <div class="contact-line">
        <svg viewBox="0 0 10 10"><rect x="0.5" y="2" width="9" height="6.5" fill="var(--brand-green)"/><path d="M0.5 2 L5 6 L9.5 2" stroke="#fff" stroke-width="1" fill="none"/></svg>
        silverharborrhythm@mailnest.net
      </div>
    </div>
    <div class="front-url">www.silverharborrhythm.net</div>
    <div class="address">Sreet Name, City Name, Zip Code-00000</div>
  </section>

  <section class="card card-back" aria-label="Card back">
    <div class="back-brand"><span class="brand-mark"></span>Silver Harbor Rhythm</div>
    <div class="back-url">www.silverharborrhythm.net</div>
  </section>
</main>
</body>
</html>
```